GTP biz card

We need a business card design for our new company based in Los Angeles called "Gold Tide Pictures". We develop film and television projects. We work with investors, financiers, film production companies, film distribution and sales companies as well as studios. We would like to incorporate our logo (see attached) on a two-sided card. We need to include: name and title, address, phone, email and company website.

Target Market(s)

Business, financial and studio clients

Industry/Entity Type

Business

Contact Information for Business Card

Two-sided. We are thinking of the logo on one side and the information on the back. Please feel free to be creative! Thanks.

Requirements
Must have
• Please include the following text information, excluding the "CAPS CATEGORY:" and please allow the ability for us to change the name, title and email address for each company employee):
• NAME & TITLE:
• Neil Parker
• Managing Partner
• COMPANY NAME:
• GOLD TIDE PICTURES (please use existing logo)
• COMPANY ADDRESS:
• KTW Studio Park
• 2250 Halverd Street
• Harbor Wing, 4th Floor
• Manhattan Beach, CA 90412
• COMPANY PHONE NUMBER:
• 310-555-0148
• COMPANY WEBSITE ADDRESS:
• www.goldtidepicturesgroup.example
• EMAIL ADDRESS: (only one per card)
• peter@goldtidepicturesgroup.example
• bingo@goldtidepicturesgroup.example
• neil@goldtidepicturesgroup.example

```html
<!DOCTYPE html>
<html lang="en">
<head>
<meta charset="utf-8">
<title>Gold Tide Pictures – Business Card</title>
<link rel="stylesheet" href="https://fonts.googleapis.com/css2?family=Questrial&family=Josefin+Sans:wght@600;700&display=swap">
<style>
  :root {
    --backdrop: #e6e6e6;
    --card: #000000;
    --ink: #ffffff;
    --accent: #2aa9e0;
    --accent-deep: #0d4f73;
    --rule: #2aa9e0;
  }
  * { box-sizing: border-box; margin: 0; padding: 0; }
  html, body { width: 1200px; height: 956px; overflow: hidden; }
  body {
    background: var(--backdrop);
    font-family: "Questrial", "Josefin Sans", sans-serif;
    color: var(--ink);
    position: relative;
  }
  .card {
    position: absolute;
    top: 102px;
    width: 420px;
    height: 720px;
    background: var(--card);
    overflow: hidden;
  }
  .card--front { left: 133px; }
  .card--back { left: 636px; }

  .brand-mark {
    position: absolute;
    left: 50%;
    border-radius: 50%;
    background: var(--accent-deep);
    transform: translateX(-50%);
  }
  .card--front .brand-mark { top: 177px; width: 200px; height: 200px; }
  .card--back .brand-mark { top: 52px; width: 152px; height: 152px; }

  .brand-name {
    position: absolute;
    left: 0; right: 0;
    text-align: center;
    color: var(--accent);
    letter-spacing: 0.06em;
    white-space: nowrap;
  }
  .card--front .brand-name { top: 395px; font-size: 30px; }
  .card--back .brand-name { top: 218px; font-size: 24px; }

  .brand-tagline {
    position: absolute;
    left: 0; right: 0;
    text-align: center;
    font-family: "Josefin Sans", sans-serif;
    font-weight: 600;
    letter-spacing: 0.24em;
    white-space: nowrap;
  }
  .card--front .brand-tagline { top: 461px; font-size: 12.5px; }
  .card--back .brand-tagline { top: 270px; font-size: 10px; }

  .person-name {
    position: absolute;
    top: 326px; left: 0; right: 0;
    text-align: center;
    font-size: 29px;
    font-weight: 400;
    letter-spacing: 0.1em;
  }
  .person-title {
    position: absolute;
    top: 362px; left: 0; right: 0;
    text-align: center;
    font-size: 18px;
    letter-spacing: 0.2em;
    color: var(--accent);
  }
  .rule {
    position: absolute;
    left: 25px; right: 25px;
    border-top: 1.5px dashed var(--rule);
  }
  .rule--top { top: 405px; }
  .rule--bottom { top: 530px; }

  .contact-list {
    position: absolute;
    top: 425px; left: 28px; right: 20px;
    list-style: none;
  }
  .contact-item {
    display: flex;
    align-items: center;
    height: 32px;
    font-family: "Josefin Sans", sans-serif;
    font-weight: 600;
    font-size: 14px;
    letter-spacing: 0.03em;
    white-space: nowrap;
  }
  .contact-item--phone { font-size: 19px; letter-spacing: 0.12em; }
  .contact-icon { width: 20px; height: 20px; margin-right: 9px; flex: none; }
  .contact-icon path, .contact-icon circle, .contact-icon rect { fill: none; stroke: var(--accent); stroke-width: 2.2; }
  .contact-icon .solid { fill: var(--accent); stroke: none; }

  .location-pin {
    position: absolute;
    top: 550px; left: 202px;
    width: 16px; height: 20px;
  }
  .location-pin path { fill: var(--accent); }
  .location-pin circle { fill: var(--card); }

  .address {
    position: absolute;
    top: 583px; left: 87px;
    font-style: normal;
    font-family: "Josefin Sans", sans-serif;
    font-weight: 600;
    font-size: 16px;
    line-height: 20px;
    letter-spacing: 0.07em;
    white-space: nowrap;
  }
  .address-venue { display: block; font-size: 20px; line-height: 24px; letter-spacing: 0.1em; font-family: "Questrial", sans-serif; }
</style>
</head>
<body>
  <section class="card card--front" aria-label="Card front">
    <div class="brand-mark" aria-hidden="true"></div>
    <p class="brand-name">GOLD TIDE PICTURES</p>
    <p class="brand-tagline">A MEDIA ENTERTAINMENT COMPANY</p>
  </section>

  <section class="card card--back" aria-label="Card back">
    <div class="brand-mark" aria-hidden="true"></div>
    <p class="brand-name">GOLD TIDE PICTURES</p>
    <p class="brand-tagline">A MEDIA ENTERTAINMENT COMPANY</p>

    <h1 class="person-name">NEIL PARKER</h1>
    <p class="person-title">MANAGING PARTNER</p>

    <div class="rule rule--top"></div>
    <ul class="contact-list">
      <li class="contact-item contact-item--phone">
        <svg class="contact-icon" viewBox="0 0 20 20" aria-hidden="true"><path class="solid" d="M4 2l3 0 1.5 4-2 1.5c1 2.3 2.7 4 5 5l1.5-2 4 1.5v3c0 1-1 2-2 2C8 17 3 12 2 4c0-1 1-2 2-2z"/></svg>
        (310) 555 0148
      </li>
      <li class="contact-item">
        <svg class="contact-icon" viewBox="0 0 20 20" aria-hidden="true"><rect x="2" y="4.5" width="16" height="11"/><path d="M2 4.5l8 6.5 8-6.5M2 15.5l6-5M18 15.5l-6-5"/></svg>
        NEIL@GOLDTIDEPICTURESGROUP.EXAMPLE
      </li>
      <li class="contact-item">
        <svg class="contact-icon" viewBox="0 0 20 20" aria-hidden="true"><circle cx="8" cy="8" r="5.5"/><path d="M12 12l6 6" stroke-linecap="round"/></svg>
        GOLDTIDEPICTURESGROUP.EXAMPLE
      </li>
    </ul>
    <div class="rule rule--bottom"></div>

    <svg class="location-pin" viewBox="0 0 16 20" aria-hidden="true"><path d="M8 0C3.6 0 0 3.4 0 7.6 0 13 8 20 8 20s8-7 8-12.4C16 3.4 12.4 0 8 0z"/><circle cx="8" cy="7.5" r="3"/></svg>
    <address class="address">
      <span class="address-venue">KTW STUDIO PARK</span>
      2250 HALVERD STREET<br>
      HARBOR WING, 4TH FLOOR<br>
      MANHATTAN BEACH, CA 90412
    </address>
  </section>
</body>
</html>
```